indépendant en tant que Massothérapeute et Préparateur Mental, j'ai besoin de ...

Massothérapeute et préparateur mental indépendant, je recherche une carte de visite sobre et dynamique, sans images liées au massage ou à la préparation mentale mais intégrant mon logo. Les couleurs que j'aime bien sont : Blanc, gris, anthracite, noir et jaune

Contact Information for Business Card

carte de préférence Horizontale
neutre qui puisse toucher le deux domaines Massothérapie et préparation mentale

Requirements
Must have
• mon projet doit intégrer au recto:
LOGO
Loïc Bardèze
078 513 26 48
info@loicbardeze.ch
et éventuellement www.loicbardeze.ch

et au verso les deux adresses:

Chemin des Ormilles 7B
1400 Yverdon-les-Bains

Route de la Gravière 9
1700 Fribourg

Should not have
• mon projet ne doit pas contenir d'image en liens avec le massage ni la préparation mentale.

```html
<!DOCTYPE html>
<html lang="fr">
<head>
<meta charset="utf-8">
<title>Loïc Bardèze – Cartes de visite</title>
<link href="https://fonts.googleapis.com/css2?family=Montserrat:wght@500;600;700&family=Arimo:wght@400&display=swap" rel="stylesheet">
<style>
  :root {
    --backdrop: #2a2a2a;
    --card: #0d0d0d;
    --card-edge: #1c1c1c;
    --silver: #e4e4e4;
    --grey: #b9b9b9;
    --rule: #6a6a6a;
    --yellow: #f2ea4a;
  }
  * { margin: 0; padding: 0; box-sizing: border-box; }
  html, body {
    width: 1200px; height: 900px; overflow: hidden;
    background: var(--backdrop);
  }
  .sheet {
    width: 1200px; height: 900px;
    display: flex; flex-direction: column;
    align-items: center; justify-content: center; gap: 40px;
  }
  .card {
    position: relative;
    width: 640px; height: 366px;
    background: radial-gradient(ellipse at 60% 30%, #1a1a1a 0%, var(--card) 70%);
    border: 1px solid var(--card-edge);
    border-radius: 22px;
    box-shadow: 0 18px 40px rgba(0,0,0,.55);
    overflow: hidden;
  }
  .brand {
    position: absolute;
    display: flex; align-items: center; gap: 14px;
  }
  .brand-dot {
    width: 34px; height: 34px; border-radius: 50%;
    background: var(--silver);
    flex: none;
  }
  .brand-name {
    font-family: "Montserrat", sans-serif;
    font-weight: 600; font-size: 30px;
    color: var(--silver); letter-spacing: .5px;
    line-height: 1;
  }
  .brand-tagline {
    font-family: "Montserrat", sans-serif;
    font-weight: 500; font-size: 9.5px;
    text-transform: uppercase; letter-spacing: 1.3px;
    color: var(--silver); margin-top: 6px;
  }
  /* Recto */
  .card-front .brand { left: 150px; top: 74px; }
  .card-front .divider {
    position: absolute; left: 330px; right: 40px; top: 176px;
    height: 1px; background: var(--rule);
  }
  .holder {
    position: absolute; left: 44px; top: 214px;
    font-family: "Montserrat", sans-serif; font-weight: 600;
    font-size: 28px; color: var(--yellow); letter-spacing: .5px;
    text-transform: uppercase;
  }
  .contacts {
    position: absolute; left: 44px; top: 262px;
    list-style: none;
    font-family: "Arimo", sans-serif; font-size: 17px; color: var(--grey);
  }
  .contacts li { display: flex; align-items: center; gap: 10px; height: 24px; }
  .contacts svg { width: 16px; height: 16px; flex: none; }
  .address {
    position: absolute;
    font-family: "Arimo", sans-serif; font-size: 17px; color: var(--grey);
    font-style: normal; line-height: 1.35;
  }
  .card-front .address { right: 40px; top: 200px; text-align: right; }
  /* Verso */
  .card-back .brand { left: 50%; top: 120px; transform: translateX(-50%); }
  .card-back .address { left: 0; right: 0; top: 230px; text-align: center; }
</style>
</head>
<body>
<main class="sheet">
  <section class="card card-front" aria-label="Recto">
    <div class="brand">
      <span class="brand-dot"></span>
      <div>
        <div class="brand-name">Loïc Bardèze</div>
        <div class="brand-tagline">Massothérapeute / Préparateur Mental</div>
      </div>
    </div>
    <span class="divider"></span>
    <h1 class="holder">Loïc Bardèze</h1>
    <ul class="contacts">
      <li>
        <svg viewBox="0 0 16 16" aria-hidden="true"><path fill="var(--yellow)" d="M3.6 1.5l2.3 2.6-1.2 1.6c.9 2 2.6 3.7 4.6 4.6l1.6-1.2 2.6 2.3-1.4 2.1C7.3 13.2 2.8 8.7 1.5 3z"/></svg>
        078 513 26 48
      </li>
      <li>
        <svg viewBox="0 0 16 16" aria-hidden="true"><rect x="1" y="3" width="14" height="10" fill="var(--yellow)"/><path d="M1 3l7 6 7-6" fill="none" stroke="#0d0d0d" stroke-width="1.3"/></svg>
        info@loicbardeze.ch
      </li>
      <li>
        <svg viewBox="0 0 16 16" aria-hidden="true"><g fill="none" stroke="var(--yellow)" stroke-width="1.4"><circle cx="8" cy="8" r="6.5"/><ellipse cx="8" cy="8" rx="2.8" ry="6.5"/><path d="M1.5 8h13M2.5 4.8h11M2.5 11.2h11"/></g></svg>
        www.loicbardeze.ch
      </li>
    </ul>
    <address class="address">Chemin des Ormilles 7B<br>1400 Yverdon-les-Bains</address>
  </section>

  <section class="card card-back" aria-label="Verso">
    <div class="brand">
      <span class="brand-dot"></span>
      <div>
        <div class="brand-name">Loïc Bardèze</div>
        <div class="brand-tagline">Massothérapeute / Préparateur Mental</div>
      </div>
    </div>
    <address class="address">Route de la Gravière 9 1700 Fribourg</address>
  </section>
</main>
</body>
</html>
```